Realty Group Needs Classy, Contemporary Letterhead Design

We need a letterhead design for a new realty company located in NY, USA. We buy investment properties to rehabilitate and or keep in our rental portfolio.

```html
<!DOCTYPE html>
<html lang="en">
<head>
<meta charset="utf-8">
<title>Meridian Realty Group – Letterhead</title>
<link href="https://fonts.googleapis.com/css2?family=Source+Sans+3:wght@300;400;700&display=swap" rel="stylesheet">
<style>
  :root {
    --backdrop: #e6e6e6;
    --paper: #ffffff;
    --brand-purple: #7b5ea7;
    --body-grey: #8c8c8c;
    --contact-grey: #8f8f8f;
    --signature-tint: #ece7f4;
  }
  * { margin: 0; padding: 0; box-sizing: border-box; }
  html, body {
    width: 1200px;
    height: 900px;
    overflow: hidden;
    background: var(--backdrop);
    font-family: "Source Sans 3", "Myriad Pro", sans-serif;
  }
  .letterhead {
    position: absolute;
    left: 303px;
    top: 30px;
    width: 594px;
    height: 840px;
    background: var(--paper);
    box-shadow: 0 6px 22px rgba(0, 0, 0, 0.18);
  }
  .brand {
    position: absolute;
    left: 41px;
    top: 50px;
    display: flex;
    align-items: center;
    gap: 8px;
  }
  .brand-mark {
    width: 12px;
    height: 12px;
    border-radius: 50%;
    background: var(--brand-purple);
  }
  .brand-name {
    font-weight: 700;
    font-size: 21px;
    letter-spacing: 0.2px;
    color: var(--brand-purple);
    line-height: 1.1;
  }
  .contact-divider {
    position: absolute;
    left: 396px;
    top: 23px;
    width: 1px;
    height: 88px;
    background: var(--brand-purple);
  }
  .contact-list {
    position: absolute;
    left: 408px;
    top: 41px;
    list-style: none;
  }
  .contact-item {
    display: flex;
    align-items: center;
    height: 20px;
    font-size: 11px;
    color: var(--contact-grey);
  }
  .contact-icon {
    width: 10px;
    height: 10px;
    margin-right: 14px;
    fill: var(--brand-purple);
  }
  .letter-body {
    position: absolute;
    left: 24px;
    top: 133px;
    width: 540px;
    font-weight: 300;
    font-size: 13.6px;
    line-height: 17.9px;
    color: var(--body-grey);
  }
  .letter-body p + p { margin-top: 17.9px; }
  .signature {
    position: absolute;
    left: 426px;
    top: 699px;
    width: 80px;
    height: 86px;
    background: var(--signature-tint);
    border-radius: 4px;
  }
  .footer-band {
    position: absolute;
    left: 0;
    bottom: 0;
    width: 100%;
    height: 4px;
    background: var(--brand-purple);
  }
</style>
</head>
<body>
  <main class="letterhead">
    <header>
      <div class="brand">
        <span class="brand-mark"></span>
        <span class="brand-name">Meridian Realty Group, LLC</span>
      </div>
      <div class="contact-divider"></div>
      <ul class="contact-list">
        <li class="contact-item">
          <svg class="contact-icon" viewBox="0 0 10 10" aria-hidden="true"><path d="M5 0.5a3.3 3.3 0 0 0-3.3 3.3C1.7 6.2 5 9.5 5 9.5s3.3-3.3 3.3-5.7A3.3 3.3 0 0 0 5 0.5zm0 4.6a1.3 1.3 0 1 1 0-2.6 1.3 1.3 0 0 1 0 2.6z"/></svg>
          Lorem ipsum
        </li>
        <li class="contact-item">
          <svg class="contact-icon" viewBox="0 0 10 10" aria-hidden="true"><path d="M3 0.5h4a0.8 0.8 0 0 1 0.8 0.8v7.4a0.8 0.8 0 0 1-0.8 0.8H3a0.8 0.8 0 0 1-0.8-0.8V1.3A0.8 0.8 0 0 1 3 0.5zm0.3 1v6.4h3.4V1.5z"/></svg>
          Lorem ipsum
        </li>
        <li class="contact-item">
          <svg class="contact-icon" viewBox="0 0 10 10" aria-hidden="true"><path d="M1 2.5h8v5H1zm0.6 0.5L5 5.6 8.4 3z" fill-rule="evenodd"/></svg>
          Lorem ipsum
        </li>
      </ul>
    </header>

    <section class="letter-body">
      <p>"Lorem ipsum dolor sit amet, consectetur adipiscing elit, sed do eiusmod tempor incididunt ut labore et dolore magna aliqua. Ut enim ad minim veniam, quis nostrud exercitation ullamco laboris nisi ut aliquip ex ea commodo consequat. Duis aute irure dolor in reprehenderit in voluptate velit esse cillum dolore eu fugiat nulla pariatur. Excepteur sint occaecat cupidatat non proident, sunt in culpa qui officia deserunt mollit anim id est laborum."</p>
      <p>Section 1.10.32 of "de Finibus Bonorum et Malorum", written by Aurelius in 45 BC<br>
      "Sed ut perspiciatis unde omnis iste natus error sit voluptatem accusantium doloremque laudantium, totam rem aperiam, eaque ipsa quae ab illo inventore veritatis et quasi architecto beatae vitae dicta sunt explicabo. Nemo enim ipsam voluptatem quia voluptas sit aspernatur aut odit aut fugit, sed quia consequuntur magni dolores eos qui ratione voluptatem sequi nesciunt. Neque porro quisquam est, qui dolorem ipsum quia dolor sit amet, consectetur, adipisci velit, sed quia non numquam eius modi tempora incidunt ut labore et dolore magnam aliquam quaerat voluptatem. Ut enim ad minima veniam, quis nostrum exercitationem ullam corporis suscipit laboriosam, nisi ut aliquid ex ea commodi consequatur? Quis autem vel eum iure reprehenderit qui in ea voluptate velit esse quam nihil molestiae consequatur, vel illum qui dolorem eum fugiat quo voluptas nulla pariatur?"</p>
      <p>1914 translation by J. Whitcombe<br>
      "But I must explain to you how all this mistaken idea of denouncing pleasure and praising pain was born and I will give you a complete account of the system, and expound the actual teachings of the great explorer of the truth, the master-builder of human happiness. No one rejects, dislikes, or avoids pleasure itself, because it is pleasure, but because those who do not know how to pursue pleasure rationally encounter consequences that are extremely painful. Nor again is there anyone who loves or pursues or desires to obtain pain of itself, because it is pain, but because occasionally circumstances occur in which toil and pain can procure him some great pleasure. To take a trivial example, which of us ever undertakes laborious physical exercise, except to obtain some advantage from it? But who has any right to find fault with a man who chooses to enjoy a pleasure that has no annoying consequences, or one who avoids a pain that produces no resultant pleasure?"</p>
    </section>

    <div class="signature" role="img" aria-label="Handwritten signature of the sender"></div>
    <div class="footer-band"></div>
  </main>
</body>
</html>
```